Letterhead and matching envelope design for a dental office

We need a new stationary design, letterhead and envelope #10, for a dental office in Denver area. We are called Bright Harbor Dental. We want a simple and minimalistic design but not a boring design. I wish to have one good point that makes it look professional. I have attached our logo. Feel free to use either one. I want the design for letterhead and envelope look like a "matching pair" but not look the same. The envelope doesn't have to be white and it will have an address window on bottom left.

Target Market(s)

everyone who visits dentist (adults)

Industry/Entity Type

Dental

Font styles to use
Other font styles liked:
• close to font on logo or something that matches well

Requirements
Must have
• professional
• simple, minimalistic
• unique point that stands out
Nice to have
• matching but not same design for letterhead and envelope
Should not have
• not look like all the other boring designs
• no flowery, distracting feats

```html
<!DOCTYPE html>
<html lang="en">
<head>
<meta charset="utf-8">
<title>Bright Harbor Dental — Stationery</title>
<link href="https://fonts.googleapis.com/css2?family=Cinzel:wght@400;600&family=Montserrat:wght@400;500&display=swap" rel="stylesheet">
<style>
  :root {
    --board: #d1d2d4;
    --green: #45b649;
    --white: #ffffff;
    --shadow: rgba(0, 0, 0, 0.28);
  }
  * { box-sizing: border-box; margin: 0; padding: 0; }
  html, body { width: 1200px; height: 927px; overflow: hidden; }
  body {
    position: relative;
    background: var(--board);
    font-family: "Montserrat", Arial, sans-serif;
  }
  .sheet {
    position: absolute;
    box-shadow: 6px 7px 10px var(--shadow);
  }
  .brand-name {
    font-family: "Cinzel", Georgia, serif;
    font-weight: 600;
    letter-spacing: 0.06em;
    white-space: nowrap;
    text-align: center;
  }
  .brand-dot {
    position: absolute;
    border-radius: 50%;
    background: var(--green);
  }
  .brand-ring {
    position: absolute;
    border-radius: 50%;
    border: 3px solid var(--white);
    display: flex; align-items: center; justify-content: center;
  }
  .brand-place {
    position: absolute; left: 0; right: 0;
    text-align: center;
    font-family: "Cinzel", Georgia, serif;
    font-weight: 400;
    font-size: 7px;
    letter-spacing: 0.9em;
    color: var(--green);
  }
  .brand-place span { background: var(--white); padding: 0 4px 0 10px; }

  /* Letterhead */
  .letterhead {
    left: 178px; top: 63px; width: 406px; height: 527px;
    background: var(--white);
  }
  .letterhead .brand-dot { left: 189px; top: 28px; width: 28px; height: 28px; }
  .letterhead .brand-name {
    position: absolute; left: 0; right: 0; top: 77px;
    font-size: 13px; color: var(--green);
  }
  .letterhead .header-rule {
    position: absolute; left: 0; right: 0; top: 96px;
    height: 1px; background: var(--green);
  }
  .letterhead .brand-place { top: 92px; }
  .letterhead .footer-rule {
    position: absolute; left: 0; right: 0; top: 479px;
    height: 2px; background: var(--green);
  }
  .letterhead .footer-band {
    position: absolute; left: 0; right: 0; top: 484px; bottom: 0;
    background: var(--green); color: var(--white);
    font-size: 9px; line-height: 11.5px;
    display: flex; justify-content: space-between; align-items: center;
    padding: 0 14px;
  }
  .postal { font-style: normal; }
  .contact-list { text-align: right; }
  .contact-line { display: flex; justify-content: flex-end; align-items: center; gap: 5px; }
  .contact-line svg { width: 7px; height: 7px; }

  /* Folder cover */
  .folder {
    left: 616px; top: 63px; width: 406px; height: 527px;
    background: var(--green);
  }
  .folder .brand-ring { left: 80px; top: 142px; width: 244px; height: 244px; }
  .folder .brand-name {
    font-size: 24px; line-height: 34px; color: var(--white);
  }
  .folder .cover-address {
    position: absolute; left: 0; right: 0; top: 492px;
    text-align: center; font-size: 9px; color: var(--white);
  }

  /* Envelope front */
  .envelope-front {
    left: 130px; top: 634px; width: 458px; height: 230px;
    background: var(--white);
  }
  .envelope-front .flap-band {
    position: absolute; left: 0; right: 0; top: 0; height: 22px;
    background: var(--green); border-radius: 14px 14px 0 0;
  }
  .envelope-front .brand-dot { left: 216px; top: 78px; width: 26px; height: 26px; }
  .envelope-front .brand-name {
    position: absolute; left: 0; right: 0; top: 135px;
    font-size: 13px; color: var(--green);
  }
  .envelope-front .brand-place { top: 152px; }
  .envelope-front .return-address {
    position: absolute; left: 0; right: 0; top: 200px;
    text-align: center; font-size: 17px; color: var(--green);
  }

  /* Envelope back */
  .envelope-back {
    left: 613px; top: 657px; width: 458px; height: 207px;
    background: var(--green);
  }
  .envelope-back .flap-band {
    position: absolute; left: 0; right: 0; top: 0; height: 22px;
    background: var(--white); border-radius: 0 0 14px 0;
  }
  .envelope-back .brand-ring {
    left: 167px; top: 54px; width: 124px; height: 124px; border-width: 2px;
  }
  .envelope-back .brand-name {
    font-size: 12px; line-height: 18px; color: var(--white);
  }
</style>
</head>
<body>

  <section class="sheet letterhead">
    <div class="brand-dot"></div>
    <div class="brand-name">Bright Harbor Dental</div>
    <div class="header-rule"></div>
    <div class="brand-place"><span>Lakewood</span></div>
    <div class="footer-rule"></div>
    <footer class="footer-band">
      <address class="postal">PO BOX 4120<br>Lakewood CO 80226</address>
      <div class="contact-list">
        <div class="contact-line">+1 303 555-0142
          <svg viewBox="0 0 10 10" aria-hidden="true"><path d="M2 1 L4 1 L4.8 3.3 L3.6 4.2 Q4.6 6 5.8 6.4 L6.7 5.2 L9 6 L9 8 Q5 9.5 1.5 4.5 Q1 2.5 2 1Z" fill="none" stroke="#fff" stroke-width="1"/></svg>
        </div>
        <div class="contact-line">info@brightharbordental.com
          <svg viewBox="0 0 10 10" aria-hidden="true"><rect x="1" y="2" width="8" height="6" fill="none" stroke="#fff" stroke-width="1"/><path d="M1 2 L5 5.5 L9 2" fill="none" stroke="#fff" stroke-width="1"/></svg>
        </div>
      </div>
    </footer>
  </section>

  <section class="sheet folder">
    <div class="brand-ring">
      <div class="brand-name">Bright<br>Harbor<br>Dental</div>
    </div>
    <div class="cover-address">PO BOX 4120 Lakewood CO 80226</div>
  </section>

  <section class="sheet envelope-front">
    <div class="flap-band"></div>
    <div class="brand-dot"></div>
    <div class="brand-name">Bright Harbor Dental</div>
    <div class="brand-place"><span>Lakewood</span></div>
    <div class="return-address">PO BOX 4120 Lakewood CO 80226</div>
  </section>

  <section class="sheet envelope-back">
    <div class="flap-band"></div>
    <div class="brand-ring">
      <div class="brand-name">Bright<br>Harbor<br>Dental</div>
    </div>
  </section>

</body>
</html>
```